New Business Card Design Project

Use the flyer uploaded and website www.brightoakbuilders.com for inspiration.
List Our Services on Backside of business cards
Marcus Delling
Harborline Builders Inc.
Licensed General Contractors
858-471-6093

Contact Information for Business Card

Use the flyer uploaded and website www.brightoakbuilders.com for inspiration. List Our Services on Backside of business cards Marcus Delling Harborline Builders Inc. Licensed General Contractors 858-471-6093

```html
<!DOCTYPE html>
<html lang="en">
<head>
<meta charset="utf-8">
<title>Harborline Builders – Business Card</title>
<link href="https://fonts.googleapis.com/css2?family=Cinzel:wght@400&family=Arimo:wght@400&display=swap" rel="stylesheet">
<style>
  :root {
    --backdrop: #dcdcdc;
    --card: #2f2f2f;
    --ink-light: #ffffff;
    --band: #e9e9eb;
    --band-ink: #2a2a2a;
  }
  * { margin: 0; padding: 0; box-sizing: border-box; }
  html, body { width: 1200px; height: 1040px; overflow: hidden; background: var(--backdrop); }
  .canvas { position: relative; width: 1200px; height: 1040px; }

  .card {
    position: absolute; left: 285px; width: 642px; height: 366px;
    background: var(--card); border-radius: 18px; overflow: hidden;
    box-shadow: 0 3px 6px rgba(0,0,0,.35);
    color: var(--ink-light);
  }
  .card--front { top: 130px; }
  .card--back { top: 568px; }

  .serif { font-family: "Cinzel", serif; font-weight: 400; }
  .sans { font-family: "Arimo", sans-serif; font-weight: 400; }

  /* front */
  .brand-name {
    position: absolute; left: 40px; width: 300px; top: 212px;
    text-align: center; font-size: 20px; letter-spacing: 1px;
  }
  .divider { position: absolute; left: 325px; top: 128px; width: 1.5px; height: 114px; background: var(--ink-light); }
  .person-name { position: absolute; left: 343px; top: 122px; font-size: 24px; letter-spacing: 1px; }
  .contact-list { position: absolute; left: 345px; top: 178px; list-style: none; font-size: 16px; line-height: 20.5px; }
  .contact-list li { display: flex; align-items: center; gap: 9px; }
  .contact-list svg { width: 13px; height: 13px; fill: var(--ink-light); flex: none; }

  .rule { position: absolute; left: 0; top: 337px; width: 100%; height: 3px; background: var(--band); }
  .footer-band {
    position: absolute; left: 0; top: 342px; width: 100%; height: 24px;
    background: var(--band); color: var(--band-ink); font-size: 14.5px;
  }
  .footer-band span { position: absolute; top: 4px; transform: translateX(-50%); white-space: nowrap; }
  .footer-company { left: 187px; }
  .footer-license { left: 430px; }

  /* back */
  .back-brand {
    position: absolute; left: 0; width: 100%; top: 110px;
    text-align: center; font-size: 34px; letter-spacing: 2px;
  }
  .services-title {
    position: absolute; left: 0; width: 100%; top: 216px;
    text-align: center; font-size: 20px; letter-spacing: 3px;
  }
  .services-list {
    position: absolute; left: 0; width: 100%; top: 253px;
    text-align: center; font-size: 16.5px; line-height: 23.4px; list-style: none;
  }
  .services-list i {
    display: inline-block; width: 7px; height: 7px; background: var(--ink-light);
    margin: 0 11px 2px; vertical-align: middle;
  }
</style>
</head>
<body>
<main class="canvas">

  <section class="card card--front" aria-label="Business card front">
    <div class="brand-name serif">HARBORLINE BUILDERS</div>
    <div class="divider"></div>
    <h1 class="person-name serif">MARCUS DELLING</h1>
    <ul class="contact-list sans">
      <li>
        <svg viewBox="0 0 24 24" aria-hidden="true"><path d="M6.6 10.8a15.1 15.1 0 0 0 6.6 6.6l2.2-2.2c.3-.3.7-.4 1-.2 1.1.4 2.3.6 3.6.6.6 0 1 .4 1 1V20c0 .6-.4 1-1 1A17 17 0 0 1 3 4c0-.6.4-1 1-1h3.5c.6 0 1 .4 1 1 0 1.3.2 2.5.6 3.6.1.3 0 .7-.2 1z"/></svg>
        858-471-6093
      </li>
      <li>
        <svg viewBox="0 0 24 24" aria-hidden="true"><path d="M2 5h20v14H2z M3.5 6.5v1l8.5 5.5 8.5-5.5v-1z" fill-rule="evenodd"/></svg>
        info@brightoakbuilders.com
      </li>
      <li>
        <svg viewBox="0 0 24 24" aria-hidden="true"><circle cx="12" cy="12" r="10"/></svg>
        www.brightoakbuilders.com
      </li>
    </ul>
    <div class="rule"></div>
    <div class="footer-band sans">
      <span class="footer-company">Harborline Builders Inc.</span>
      <span class="footer-license">Licensed General Contractors</span>
    </div>
  </section>

  <section class="card card--back" aria-label="Business card back">
    <div class="back-brand serif">HARBORLINE BUILDERS</div>
    <h2 class="services-title serif">SERVICES</h2>
    <ul class="services-list sans">
      <li>Remodel : Kitchen &amp; Bath<i></i>Painting : Interior &amp; Exterior</li>
      <li>Flooring : Carpet, Vinyl, Wood<i></i>Window &amp; Door Replacement</li>
      <li>Plumbing : Repairs &amp; Upgrades<i></i>Energy- Efficient Upgrades</li>
      <li>Deck &amp; Patio Construction<i></i>Water &amp; Mold Damage<i></i>Garage Renovation</li>
    </ul>
  </section>

</main>
</body>
</html>
```